Aunt Wilma's Ember-Kissed Husk Shack Concession Trailer Logo Wraps

Looking to put my design concept into a final production-ready format for vinyl-based logo "wrap" on the exterior of a 7x12 black concession trailer selling farm-fresh corn on the cob slathered in flavor flamboyance, corn in a cup, corn over crushed snacks (Crunvels, Zaplins, Puffnars, etc.) served in the bags, fire-roasted street corn (Mexican elotes), corn grits, corn chowder, cornbread, corndogs. I have my fonts and colors and a flame graphic I've roughly edited/reworked attempting to make it work and need a design pro to bring it all together for me. The approximate size of the graphics on the four sides of the trailer will be: the serving window when closed (48"L x 24"H); front (48"x48"); full right side (11'x5'); door (6'x2') and possibly the left side next to door (3'x5'). Pictures uploaded.
Target Market(s)
Food truck festivals, private catering gigs, fairs, farm markets, concerts, etc.
Font styles to use
Other font styles liked:
- flame fetish, Algerian
Requirements
Must have
- My color scheme as depicted in uploaded files, flame fetish font uploaded (will consider similar fonts), flame/fire artwork, bright bold colors that pop against a black background
Nice to have
- straight line of flames on each side of the "fire-roasted" text, flowing from the first and last letter

```html
<!DOCTYPE html>
<html lang="en">
<head>
<meta charset="utf-8">
<title>Aunt Wilma's Ember-Kissed Husk Shack – Service Window Side</title>
<link rel="stylesheet" href="https://fonts.googleapis.com/css2?family=Baloo+2:wght@800&family=Anton&family=Oswald:wght@400;500;600&family=Open+Sans:wght@600;700&display=swap">
<style>
  :root {
    --paper: #ffffff;
    --ink: #111111;
    --frame-face: #b8c2c9;
    --panel: #131313;
    --sky-blue: #1aa3d6;
    --corn-gold: #fcd22c;
    --ember-orange: #ff8a2a;
    --ember-mid: #e2581a;
    --ember-hot: #ffb02e;
    --mark-red: #d8232a;
    --shelf: #a1a1a5;
    --plate-light: #e6e9ec;
    --plate-mid: #b9bfc5;
    --white: #ffffff;
  }
  html, body {
    margin: 0;
    padding: 0;
    width: 1200px;
    height: 776px;
    overflow: hidden;
    background: var(--paper);
  }
  .elevation { display: block; width: 1200px; height: 776px; }
  .dim-line { stroke: var(--ink); stroke-width: 1.4; fill: none; }
  .dim-label { font-family: "Oswald", sans-serif; font-size: 10px; fill: var(--ink); text-anchor: middle; }
  .frame-face { fill: var(--frame-face); stroke: var(--ink); stroke-width: 1; }
  .frame-miter { stroke: var(--ink); stroke-width: 1; }
  .sign-panel { fill: var(--panel); }
  .brand-name { font-family: "Baloo 2", "Arial Rounded MT Bold", sans-serif; font-weight: 800; font-size: 50px; fill: var(--sky-blue); text-anchor: middle; }
  .brand-accent { font-family: "Oswald", "Arial Narrow", sans-serif; font-weight: 600; font-size: 26px; letter-spacing: 6px; fill: var(--white); text-anchor: middle; }
  .brand-block { font-family: "Anton", "Impact", sans-serif; font-size: 52px; fill: var(--corn-gold); text-anchor: middle; }
  .brand-tagline { font-family: "Oswald", "Arial Narrow", sans-serif; font-weight: 400; font-size: 16px; letter-spacing: 1px; fill: var(--ember-orange); text-anchor: middle; }
  .placeholder-box { fill: none; stroke: var(--mark-red); stroke-width: 1.2; }
  .strike { stroke: var(--mark-red); stroke-width: 1; }
  .shelf { fill: var(--shelf); }
  .shelf-leg { fill: var(--shelf); stroke: #6e6e72; stroke-width: 0.8; }
  .social-band { fill: var(--panel); stroke: var(--mark-red); stroke-width: 1.2; }
  .social-head { font-family: "Open Sans", sans-serif; font-weight: 700; font-size: 9.5px; fill: var(--corn-gold); }
  .social-line { font-family: "Open Sans", sans-serif; font-weight: 600; font-size: 6px; fill: var(--white); }
  .social-dot { fill: var(--sky-blue); }
  .art-fill { fill: url(#artTones); }
  .art-caption { font-family: "Open Sans", sans-serif; font-weight: 700; font-size: 10px; fill: var(--white); text-anchor: middle; }
  .tread-plate { fill: url(#plateTone); stroke: #9aa1a8; stroke-width: 0.8; }
  .spec-card { fill: var(--paper); stroke: var(--ink); stroke-width: 1; }
  .spec-title, .spec-text { font-family: "Oswald", sans-serif; fill: var(--ink); }
  .spec-title { font-size: 20px; }
  .spec-text { font-size: 21px; }
</style>
</head>
<body>
<svg class="elevation" viewBox="0 0 1200 776" xmlns="http://www.w3.org/2000/svg">
  <defs>
    <linearGradient id="flameBand" x1="0" y1="0" x2="0" y2="1">
      <stop offset="0" stop-color="#131313" stop-opacity="0"/>
      <stop offset="0.45" stop-color="#e2581a" stop-opacity="0.85"/>
      <stop offset="1" stop-color="#ffb02e"/>
    </linearGradient>
    <linearGradient id="flameGlow" x1="0" y1="0" x2="0" y2="1">
      <stop offset="0" stop-color="#e2581a" stop-opacity="0.55"/>
      <stop offset="1" stop-color="#131313" stop-opacity="0"/>
    </linearGradient>
    <linearGradient id="artTones" x1="0" y1="0" x2="1" y2="1">
      <stop offset="0" stop-color="#1b1b1b"/>
      <stop offset="0.55" stop-color="#5c4a44"/>
      <stop offset="1" stop-color="#c8602a"/>
    </linearGradient>
    <linearGradient id="plateTone" x1="0" y1="0" x2="1" y2="0">
      <stop offset="0" stop-color="#b9bfc5"/>
      <stop offset="0.5" stop-color="#e6e9ec"/>
      <stop offset="1" stop-color="#b9bfc5"/>
    </linearGradient>
    <clipPath id="artClip"><rect x="146" y="405" width="170" height="191"/></clipPath>
  </defs>

  <g class="dimensions-horizontal">
    <text class="dim-label" x="630" y="45">140.0”</text>
    <line class="dim-line" x1="137" y1="56" x2="1146" y2="56"/>
    <line class="dim-line" x1="137" y1="78" x2="1146" y2="78"/>
    <line class="dim-line" x1="146" y1="45" x2="146" y2="83"/>
    <line class="dim-line" x1="1137" y1="45" x2="1137" y2="83"/>
    <line class="dim-line" x1="358" y1="65" x2="358" y2="82"/>
    <line class="dim-line" x1="401" y1="65" x2="401" y2="82"/>
    <line class="dim-line" x1="863" y1="65" x2="863" y2="82"/>
    <line class="dim-line" x1="904" y1="65" x2="904" y2="82"/>
    <line class="dim-line" x1="925" y1="65" x2="925" y2="82"/>
    <line class="dim-line" x1="1116" y1="65" x2="1116" y2="82"/>
    <text class="dim-label" x="250" y="74">30.0”</text>
    <text class="dim-label" x="630" y="74">65.0”</text>
    <text class="dim-label" x="915" y="74">3”</text>
    <text class="dim-label" x="1024" y="74">27.0”</text>
    <text class="dim-label" x="1127" y="74">3”</text>
  </g>

  <g class="dimensions-vertical">
    <line class="dim-line" x1="102" y1="87" x2="102" y2="606"/>
    <line class="dim-line" x1="131" y1="87" x2="131" y2="606"/>
    <line class="dim-line" x1="94" y1="93" x2="133" y2="93"/>
    <line class="dim-line" x1="116" y1="135" x2="133" y2="135"/>
    <line class="dim-line" x1="116" y1="179" x2="133" y2="179"/>
    <line class="dim-line" x1="116" y1="388" x2="133" y2="388"/>
    <line class="dim-line" x1="116" y1="435" x2="133" y2="435"/>
    <line class="dim-line" x1="116" y1="471" x2="133" y2="471"/>
    <line class="dim-line" x1="116" y1="482" x2="133" y2="482"/>
    <line class="dim-line" x1="94" y1="596" x2="133" y2="596"/>
    <text class="dim-label" x="118" y="118">6.0”</text>
    <text class="dim-label" x="118" y="284">30.0”</text>
    <text class="dim-label" x="83" y="340">71.0”</text>
    <text class="dim-label" x="118" y="455">5.0”</text>
    <text class="dim-label" x="118" y="541">16.0”</text>
  </g>

  <g class="main-sign">
    <rect class="frame-face" x="358" y="134" width="546" height="300"/>
    <rect class="frame-face" x="382" y="159" width="498" height="251"/>
    <line class="frame-miter" x1="358" y1="134" x2="401" y2="178"/>
    <line class="frame-miter" x1="904" y1="134" x2="861" y2="178"/>
    <line class="frame-miter" x1="358" y1="434" x2="401" y2="391"/>
    <line class="frame-miter" x1="904" y1="434" x2="861" y2="391"/>
    <rect class="sign-panel" x="401" y="178" width="460" height="213"/>
    <rect role="img" aria-label="Flame artwork rising along the horizon line" x="401" y="213" width="460" height="81" fill="url(#flameBand)"/>
    <rect x="401" y="294" width="460" height="32" fill="url(#flameGlow)"/>
    <line x1="401" y1="294" x2="861" y2="294" stroke="#5a3a22" stroke-width="0.8"/>
    <text class="brand-name" x="630" y="246">Aunt Wilma's</text>
    <text class="brand-accent" x="630" y="287">EMBER-KISSED</text>
    <text class="brand-block" x="630" y="352" textLength="380" lengthAdjust="spacingAndGlyphs">HUSK SHACK</text>
    <text class="brand-tagline" x="630" y="378">Sweet corn, smoky char &amp; big-hearted flavor</text>
  </g>

  <rect class="placeholder-box" x="925" y="178" width="191" height="276"/>

  <g class="service-shelf">
    <rect class="shelf" x="344" y="470" width="581" height="11"/>
    <rect class="shelf-leg" x="358" y="481" width="13" height="52"/>
    <rect class="shelf-leg" x="891" y="481" width="13" height="52"/>
  </g>

  <g class="social-strip">
    <rect class="social-band" x="925" y="491" width="191" height="36"/>
    <text class="social-head" x="930" y="505" textLength="181" lengthAdjust="spacing">AVAILABLE FOR PRIVATE EVENTS</text>
    <circle class="social-dot" cx="969" cy="519" r="2.2"/>
    <text class="social-line" x="930" y="521">Follow us on</text>
    <text class="social-line" x="974" y="521" textLength="137" lengthAdjust="spacingAndGlyphs">Chatterbook  Snapgram  #aunt_wilma  #huskshackeats</text>
    <line class="strike" x1="925" y1="491" x2="1116" y2="527"/>
    <line class="strike" x1="925" y1="527" x2="1116" y2="491"/>
  </g>

  <g class="character-graphic" clip-path="url(#artClip)">
    <rect class="art-fill" role="img" aria-label="Illustrated mascot graphic of Aunt Wilma, approx. 24 by 27 inch area" x="146" y="405" width="170" height="191"/>
    <line class="strike" x1="146" y1="405" x2="316" y2="596"/>
    <line class="strike" x1="146" y1="596" x2="316" y2="405"/>
    <rect x="146" y="405" width="170" height="191" fill="none" stroke="#d8232a" stroke-width="1"/>
    <text class="art-caption" x="259" y="414">Graphic # 2</text>
    <text class="art-caption" x="259" y="426">Aunt Wilma Graphics</text>
    <text class="art-caption" x="259" y="438">(24”x 27”) approx. area</text>
  </g>

  <rect class="tread-plate" role="img" aria-label="Diamond tread plate skirt" x="146" y="596" width="991" height="94"/>

  <g class="spec-card-group">
    <rect class="spec-card" x="221" y="624" width="256" height="132"/>
    <text class="spec-title" x="232" y="651">SERVICE WINDOW SIDE</text>
    <text class="spec-text" x="232" y="699">MAIN VISUAL:</text>
    <text class="spec-text" x="374" y="699">65.0” X 30.0”</text>
    <text class="spec-text" x="232" y="723">AUNT WILMA:</text>
    <text class="spec-text" x="374" y="723">24.0’ X 27.0”</text>
    <text class="spec-text" x="232" y="747">SOCIAL MEDIA:</text>
    <text class="spec-text" x="374" y="747">27.0 X 5.0”</text>
  </g>
</svg>
</body>
</html>
```